Popcorn, ice cream, alcohol infused shakes shop

Create a clean simple website with pictures and bold type for a popcorn, ice cream and boozy shake shop. The site should have:
- Unique and Large Typography
- Large & Responsive Hero (stunning, elicits a response) Images.No concern with above or below the fold. Create a strong visual experience that encourages visitors to scroll down to read more. Use large images to visually tell a story without having to rely on just text.
- Flat image designs
- Place for me to upload an ad type video
- Hidden type menu (three line menu)
- A few small card like images (food, gift bags, tins, etc.) menu items with a brief description.

Target Market(s)

21-49 years of age for the boozy shakes. Soccer moms for sports teams & sleepovers, professionals (teachers, realtors, pharm sales), gifts for family and friends. Also some kids

Coding

Coded - Design and coding required

Number of Pages Required

5+ page

Font styles to use
Sans Serif

Colors

Designer to choose colors to be used in the design.

Requirements
Must have
• Images of gourmet popcorn, fancy shakes, ice cream, gift bags and popcorn tins. Holiday popcorn tins and gift bags along with grift certificates. Ability for visitors to send a contact form to kt@treatloft.example
• Five pages - Home Page, AboutUs, Menu, Gift/Promotion, Contact Us
Nice to have
• Smooth flow on the home page. Mostly images and bold text.
Should not have
• Too many words. Boring text fonts

```html
<!DOCTYPE html>
<html lang="en">
<head>
<meta charset="utf-8">
<title>Treat Loft — Website Presentation</title>
<link href="https://fonts.googleapis.com/css2?family=Bebas+Neue&family=Poppins:wght@400;500;600&display=swap" rel="stylesheet">
<style>
:root{
  --orange:#F7981D;
  --navy:#252A5B;
  --ink:#262626;
  --muted:#5a4a3a;
  --board:#f2f2f2;
  --white:#ffffff;
  --field:#c9c9c9;
}
*{box-sizing:border-box;margin:0;padding:0}
html,body{width:1200px;height:3970px;overflow:hidden}
body{background:var(--board);font-family:"Poppins",sans-serif;color:var(--ink);position:relative}
.abs{position:absolute}
.display{font-family:"Bebas Neue",sans-serif;line-height:.9;font-weight:400}
.orange-text{color:var(--orange)}
.white-text{color:var(--white)}
.copy{font-size:8px;line-height:1.55;color:#555}
.copy-sm{font-size:5px;line-height:1.55;color:#555}
.brand{font-family:"Bebas Neue",sans-serif;color:var(--orange);line-height:.85;letter-spacing:1px}
.pill{position:absolute;border-radius:20px;background:var(--orange);color:var(--white);font-size:7px;display:flex;align-items:center;justify-content:center}
.pill-outline{border-radius:20px;border:1.4px solid #4a3a2a;color:#3a2a1a;display:flex;align-items:center;justify-content:center;margin:0 auto}
.circle{position:absolute;border-radius:50%}
.navy-dot{background:var(--navy)}
.orange-dot{background:var(--orange)}
.ringed-navy{box-shadow:0 0 0 5px var(--white),0 0 0 6px var(--navy)}
.ringed-orange{box-shadow:0 0 0 5px var(--white),0 0 0 6px var(--orange)}
.burger{position:absolute;display:flex;align-items:center;gap:6px}
.burger-lines{width:12px;height:9px;border-top:2px solid var(--orange);border-bottom:2px solid var(--orange);position:relative}
.burger-lines::after{content:"";position:absolute;left:0;right:0;top:1.5px;border-top:2px solid var(--orange)}
.search{width:8px;height:8px;border:1.6px solid var(--ink);border-radius:50%;position:relative}
.search::after{content:"";position:absolute;width:4px;height:1.6px;background:var(--ink);transform:rotate(45deg);right:-4px;bottom:-2px}
.dots{position:absolute;display:flex;gap:4px}
.dots i{width:5px;height:5px;border-radius:50%;background:#bbb;display:block}
.dots i.on{background:var(--navy)}

/* photo placeholders */
.photo-icecream{background:radial-gradient(circle at 40% 45%,#f3b6c4,#e7c98c 55%,#8fc46a 80%,#e8d7c7)}
.photo-chef{background:radial-gradient(circle at 50% 50%,#f2efe9,#c9c3b8 60%,#7d7a73)}
.photo-popcorn{background:radial-gradient(circle at 50% 40%,#fff3cf,#f1d48a 55%,#d9403a 85%)}
.photo-cone{background:radial-gradient(circle at 50% 45%,#f5f0e6,#a6d7e6 45%,#c7914e 80%)}
.photo-shake{background:radial-gradient(circle at 50% 45%,#fbe3ea,#f2b6c6 50%,#f4f1ee 85%)}
.photo-tart{background:radial-gradient(circle at 50% 50%,#f7d3d6,#e5717f 45%,#f0ece6 85%)}
.photo-soda{background:radial-gradient(circle at 50% 50%,#f2f2f2,#7a3a22 45%,#d0322b 75%,#f4f4f4)}
.g-cupcakes{background:linear-gradient(135deg,#3b2a2c,#b8414a 55%,#d9c7c3)}
.g-bags{background:linear-gradient(135deg,#f4efe6,#cf9a55 55%,#e8d1a6)}
.g-cake{background:linear-gradient(135deg,#4e6d86,#f1ece5 45%,#9a6a45)}
.g-cocoa{background:linear-gradient(135deg,#f6f3ef,#8a5a3c 55%,#f0ebe6)}
.g-fire{background:linear-gradient(135deg,#2a1a14,#c2421f 50%,#f0c25b)}
.g-berry{background:linear-gradient(135deg,#f8f1f0,#f0a7b6 50%,#c8303b)}

/* frames */
.screen{position:absolute;background:var(--white);overflow:hidden}
.desktop{left:365px;top:77px;width:741px;height:3800px}
.mobile{left:92px;top:282px;width:193px;height:2957px}
.shape-layer{position:absolute;left:0;top:0}

/* deals */
.deal{position:absolute;width:240px;text-align:center}
.deal .circle{position:relative;width:170px;height:170px;margin:0 auto;display:block}
.deal h3{font-family:"Bebas Neue",sans-serif;font-weight:400;font-size:36px;line-height:1;margin-top:16px;color:var(--ink)}
.deal p{font-size:7px;line-height:1.6;color:#4a3a2a;width:190px;margin:6px auto 10px}
.deal .pill-outline{width:103px;height:26px;font-size:7px}
.deal-m{position:absolute;width:150px;text-align:center;left:20px}
.deal-m .circle{position:relative;width:96px;height:96px;margin:0 auto;display:block}
.deal-m h3{font-family:"Bebas Neue",sans-serif;font-weight:400;font-size:22px;line-height:1;margin-top:12px;color:var(--ink)}
.deal-m p{font-size:4.5px;line-height:1.6;color:#4a3a2a;width:110px;margin:4px auto 6px}
.deal-m .pill-outline{width:62px;height:12px;font-size:4px;border-width:1px}
.divider{position:absolute;width:1px;background:#c46f0f}

/* gallery */
.gallery-card{position:absolute;background:var(--white);border-radius:60px;box-shadow:0 10px 30px rgba(0,0,0,.08)}
.tile{position:absolute;border-radius:4px}

/* contact */
.field{position:absolute;border:1px solid var(--field);border-radius:12px;font-size:6.5px;color:#999;padding:0 10px;display:flex;align-items:center}
.field.message{align-items:flex-start;padding-top:9px}
.field-m{border-radius:6px;font-size:3.5px;padding:0 5px}
.field-m.message{padding-top:4px}

/* footer */
.foot-title{font-family:"Poppins",sans-serif;font-weight:600;font-size:8px;color:var(--ink)}
.foot-links{list-style:none;font-size:6px;line-height:2.25;color:#4a3a2a}
.social{display:flex;gap:3px}
.social i{display:block;width:8px;height:8px;border-radius:50%;background:var(--ink)}
</style>
</head>
<body>

<!-- Brand mark -->
<div class="abs brand" style="left:70px;top:78px;font-size:84px;">TREAT<br>LOFT</div>

<!-- ============ MOBILE ============ -->
<section class="screen mobile" aria-label="Mobile layout">
  <svg class="shape-layer" width="193" height="2957" viewBox="0 0 193 2957" aria-hidden="true">
    <path d="M0,873 Q60,852 193,850 L193,2260 Q100,2235 0,2250 Z" fill="#F7981D"/>
    <path d="M0,2672 Q96,2620 193,2672 L193,2957 L0,2957 Z" fill="#F7981D"/>
  </svg>

  <div class="abs brand" style="left:15px;top:12px;font-size:12px;">TREAT<br>LOFT</div>
  <div class="burger" style="left:151px;top:19px;transform:scale(.7);transform-origin:left top"><span class="burger-lines"></span><span class="search"></span></div>

  <div class="circle navy-dot" style="left:111px;top:48px;width:86px;height:86px"></div>
  <div class="circle photo-icecream" style="left:43px;top:82px;width:114px;height:114px" role="img" aria-label="Photo of ice cream cups with sprinkles and waffle cones"></div>
  <div class="circle orange-dot" style="left:111px;top:164px;width:50px;height:50px"></div>

  <h1 class="abs display" style="left:15px;top:210px;font-size:33px">WE ARE</h1>
  <div class="abs display orange-text" style="left:15px;top:239px;font-size:48px">FOOD</div>
  <div class="abs display" style="left:15px;top:278px;font-size:48px">MASTERS</div>
  <p class="abs copy-sm" style="left:15px;top:332px;width:140px">Handmade popcorn, creamy scoops and grown-up shakes made fresh every day in small batches for sharing with friends.</p>
  <div class="pill" style="left:15px;top:371px;width:74px;height:18px;font-size:4px">Order Now</div>
  <div class="dots" style="left:86px;top:429px;transform:scale(.7)"><i></i><i class="on"></i><i></i></div>

  <div class="circle photo-chef" style="left:0;top:458px;width:138px;height:138px" role="img" aria-label="Photo of a smiling chef in a white jacket"></div>
  <div class="circle navy-dot ringed-navy" style="left:24px;top:580px;width:50px;height:50px;box-shadow:0 0 0 3px #fff,0 0 0 4px var(--navy)"></div>
  <h2 class="abs display" style="left:63px;top:634px;font-size:46px">ABOUT</h2>
  <div class="abs display orange-text" style="left:63px;top:674px;font-size:46px">US</div>
  <p class="abs copy-sm" style="left:63px;top:727px;width:112px">We are a small family shop that pops, churns and blends every treat by hand, with recipes built over years of sleepovers and game days.</p>
  <div class="pill" style="left:63px;top:781px;width:72px;height:18px;font-size:4px">View More</div>

  <h2 class="abs display" style="left:0;width:193px;text-align:center;top:913px;font-size:46px">DEALS AND</h2>
  <div class="abs display white-text" style="left:0;width:193px;text-align:center;top:950px;font-size:46px">OFFERS</div>
  <p class="abs copy-sm" style="left:30px;width:133px;text-align:center;top:1015px;color:#4a3a2a">Fresh seasonal deals on popcorn tins, gift bags and shakes. Grab a bundle for team nights, sleepovers, holidays or a simple thank you.</p>

  <div class="deal-m" style="top:1076px"><span class="circle photo-popcorn" role="img" aria-label="Photo of a striped popcorn box"></span><h3>POPCORN</h3><p>Small batch treats made fresh daily, ready to share or gift.</p><div class="pill-outline">Categories</div></div>
  <div class="deal-m" style="top:1279px"><span class="circle photo-cone" role="img" aria-label="Photo of ice cream in a waffle cone with sprinkles"></span><h3>POPCORN</h3><p>Small batch treats made fresh daily, ready to share or gift.</p><div class="pill-outline">Categories</div></div>
  <div class="deal-m" style="top:1482px"><span class="circle photo-shake" role="img" aria-label="Photo of a pink strawberry shake"></span><h3>POPCORN</h3><p>Small batch treats made fresh daily, ready to share or gift.</p><div class="pill-outline">Categories</div></div>
  <div class="deal-m" style="top:1684px"><span class="circle photo-tart" role="img" aria-label="Photo of frosted pop tart pastries"></span><h3>POPCORN</h3><p>Small batch treats made fresh daily, ready to share or gift.</p><div class="pill-outline">Categories</div></div>
  <div class="deal-m" style="top:1888px"><span class="circle photo-soda" role="img" aria-label="Photo of a soda glass with ice and cans"></span><h3>POPCORN</h3><p>Small batch treats made fresh daily, ready to share or gift.</p><div class="pill-outline">Categories</div></div>

  <div class="gallery-card" style="left:18px;top:2097px;width:156px;height:308px;border-radius:22px"></div>
  <div class="circle navy-dot" style="left:132px;top:2090px;width:62px;height:62px;box-shadow:0 0 0 3px #fff,0 0 0 4px var(--navy)"></div>
  <h2 class="abs display" style="left:28px;top:2137px;font-size:40px">OUR</h2>
  <div class="abs display orange-text" style="left:28px;top:2168px;font-size:40px">GALLARIES</div>
  <div class="tile g-cupcakes" style="left:28px;top:2231px;width:66px;height:41px" role="img" aria-label="Photo of cupcakes on a glass stand"></div>
  <div class="tile g-bags" style="left:100px;top:2231px;width:64px;height:41px" role="img" aria-label="Photo of kraft paper gift bags"></div>
  <div class="tile g-cake" style="left:28px;top:2283px;width:66px;height:41px" role="img" aria-label="Photo of a layered cake slice"></div>
  <div class="tile g-cocoa" style="left:100px;top:2283px;width:64px;height:41px" role="img" aria-label="Photo of a chocolate shake with chocolate pieces"></div>
  <div class="tile g-fire" style="left:28px;top:2332px;width:66px;height:41px" role="img" aria-label="Photo of popcorn bowls by a fireplace"></div>
  <div class="tile g-berry" style="left:100px;top:2332px;width:64px;height:41px" role="img" aria-label="Photo of strawberry mousse dessert"></div>

  <h2 class="abs foot-title" style="left:0;width:193px;text-align:center;top:2428px;font-family:'Bebas Neue',sans-serif;font-weight:400;font-size:20px">CONTACT <span class="orange-text">US</span></h2>
  <div class="field field-m" style="left:43px;top:2470px;width:106px;height:14px">Name*</div>
  <div class="field field-m" style="left:43px;top:2490px;width:106px;height:14px">Email*</div>
  <div class="field field-m" style="left:43px;top:2509px;width:106px;height:14px">Phone No.</div>
  <div class="field field-m" style="left:43px;top:2529px;width:106px;height:14px">Address</div>
  <div class="field field-m message" style="left:43px;top:2549px;width:106px;height:54px">Message</div>
  <div class="pill" style="left:68px;top:2615px;width:55px;height:15px;font-size:4px">Send</div>

  <div class="abs brand" style="left:15px;top:2706px;font-size:16px;">TREAT<br>LOFT</div>
  <p class="abs copy-sm" style="left:15px;top:2752px;width:125px;color:#4a3a2a">Popcorn, ice cream and shakes made by hand in small batches, packed in tins and bags that make every visit a little sweeter.</p>
  <div class="abs foot-title" style="left:15px;top:2818px;font-size:6px">QUICK LINKS</div>
  <ul class="abs foot-links" style="left:15px;top:2838px;font-size:4.5px">
    <li>Home</li><li>About Us</li><li>Menu</li><li>Gift/Promotion</li><li>Contact Us</li>
  </ul>
  <div class="abs foot-title" style="left:106px;top:2818px;font-size:6px">CONNECT US</div>
  <div class="abs social" style="left:106px;top:2842px;transform:scale(.7);transform-origin:left top"><i></i><i></i><i></i></div>
  <p class="abs copy-sm" style="left:106px;top:2852px;width:70px;color:#4a3a2a">Treat Loft Copyright<br>© 2019</p>
</section>

<!-- ============ DESKTOP ============ -->
<section class="screen desktop" aria-label="Desktop layout">
  <svg class="shape-layer" width="741" height="3800" viewBox="0 0 741 3800" aria-hidden="true">
    <path d="M0,1109 C180,960 430,875 741,858 L741,2641 C480,2600 220,2490 0,2387 Z" fill="#F7981D"/>
    <path d="M0,3681 Q370,3479 741,3681 L741,3800 L0,3800 Z" fill="#F7981D"/>
  </svg>

  <header>
    <div class="abs brand" style="left:92px;top:12px;font-size:18px;">TREAT<br>LOFT</div>
    <nav class="burger" style="left:618px;top:23px" aria-label="Menu"><span class="burger-lines"></span><span class="search"></span></nav>
  </header>

  <!-- Hero -->
  <div class="circle navy-dot ringed-navy" style="left:556px;top:96px;width:192px;height:192px"></div>
  <div class="circle photo-icecream" style="left:392px;top:165px;width:256px;height:256px" role="img" aria-label="Photo of ice cream cups with sprinkles and waffle cones"></div>
  <div class="circle orange-dot ringed-orange" style="left:548px;top:346px;width:114px;height:114px"></div>

  <h1 class="abs display" style="left:90px;top:117px;font-size:66px">WE ARE</h1>
  <div class="abs display orange-text" style="left:90px;top:185px;font-size:88px">FOOD</div>
  <div class="abs display" style="left:90px;top:266px;font-size:88px">MASTERS</div>
  <p class="abs copy" style="left:92px;top:357px;width:285px;font-size:7px">Handmade popcorn, creamy scoops and grown-up shakes made fresh every day in small batches for sharing with friends.</p>
  <div class="pill" style="left:92px;top:408px;width:103px;height:26px">Order Now</div>
  <div class="dots" style="left:358px;top:465px"><i></i><i class="on"></i><i></i></div>

  <!-- About -->
  <div class="circle photo-chef" style="left:12px;top:525px;width:318px;height:318px" role="img" aria-label="Photo of a smiling chef in a white jacket"></div>
  <div class="circle navy-dot ringed-navy" style="left:71px;top:802px;width:114px;height:114px"></div>
  <h2 class="abs display" style="left:366px;top:540px;font-size:88px">ABOUT</h2>
  <div class="abs display orange-text" style="left:366px;top:622px;font-size:88px">US</div>
  <p class="abs copy" style="left:368px;top:714px;width:285px;font-size:7px">We are a small family shop that pops, churns and blends every treat by hand, with recipes built over years of sleepovers and game days.</p>
  <div class="pill" style="left:368px;top:771px;width:103px;height:26px">View More</div>

  <!-- Deals -->
  <h2 class="abs display" style="left:0;width:741px;text-align:center;top:1036px;font-size:88px">DEALS AND</h2>
  <div class="abs display white-text" style="left:0;width:741px;text-align:center;top:1116px;font-size:88px">OFFERS</div>
  <p class="abs copy" style="left:160px;width:421px;text-align:center;top:1214px;font-size:7px;color:#4a3a2a">Fresh seasonal deals on popcorn tins, gift bags and shakes. Grab a bundle for team nights, sleepovers, holidays or a simple thank you.</p>

  <div class="divider" style="left:371px;top:1352px;height:129px"></div>
  <div class="divider" style="left:371px;top:1714px;height:129px"></div>

  <div class="deal" style="left:116px;top:1293px"><span class="circle photo-popcorn" role="img" aria-label="Photo of a striped popcorn box"></span><h3>POPCORN</h3><p>Small batch treats made fresh daily, ready to share or gift.</p><div class="pill-outline">Categories</div></div>
  <div class="deal" style="left:387px;top:1293px"><span class="circle photo-cone" role="img" aria-label="Photo of ice cream in a waffle cone with sprinkles"></span><h3>ICE CREAM</h3><p>Small batch treats made fresh daily, ready to share or gift.</p><div class="pill-outline">Categories</div></div>
  <div class="deal" style="left:116px;top:1655px"><span class="circle photo-shake" role="img" aria-label="Photo of a pink strawberry shake"></span><h3>SHAKES</h3><p>Small batch treats made fresh daily, ready to share or gift.</p><div class="pill-outline">Categories</div></div>
  <div class="deal" style="left:387px;top:1655px"><span class="circle photo-tart" role="img" aria-label="Photo of frosted pop tart pastries"></span><h3>POP TARTS</h3><p>Small batch treats made fresh daily, ready to share or gift.</p><div class="pill-outline">Categories</div></div>
  <div class="deal" style="left:251px;top:1997px"><span class="circle photo-soda" role="img" aria-label="Photo of a soda glass with ice and cans"></span><h3>SODAS/WATER</h3><p>Small batch treats made fresh daily, ready to share or gift.</p><div class="pill-outline">Categories</div></div>

  <!-- Gallery -->
  <div class="gallery-card" style="left:92px;top:2402px;width:556px;height:770px"></div>
  <div class="circle navy-dot ringed-navy" style="left:577px;top:2455px;width:148px;height:148px"></div>
  <h2 class="abs display" style="left:146px;top:2464px;font-size:88px">OUR</h2>
  <div class="abs display orange-text" style="left:146px;top:2543px;font-size:88px">GALLARIES</div>
  <div class="tile g-cupcakes" style="left:148px;top:2660px;width:217px;height:143px" role="img" aria-label="Photo of cupcakes on a glass stand"></div>
  <div class="tile g-bags" style="left:374px;top:2660px;width:217px;height:143px" role="img" aria-label="Photo of kraft paper gift bags"></div>
  <div class="tile g-cake" style="left:148px;top:2812px;width:217px;height:143px" role="img" aria-label="Photo of a layered cake slice"></div>
  <div class="tile g-cocoa" style="left:374px;top:2812px;width:217px;height:143px" role="img" aria-label="Photo of a chocolate shake with chocolate pieces"></div>
  <div class="tile g-fire" style="left:148px;top:2963px;width:217px;height:143px" role="img" aria-label="Photo of popcorn bowls by a fireplace"></div>
  <div class="tile g-berry" style="left:374px;top:2963px;width:217px;height:143px" role="img" aria-label="Photo of strawberry mousse dessert"></div>

  <!-- Contact -->
  <h2 class="abs display" style="left:0;width:741px;text-align:center;top:3232px;font-size:36px">CONTACT <span class="orange-text">US</span></h2>
  <form aria-label="Contact form to kt@treatloft.example">
    <div class="field" style="left:159px;top:3303px;width:208px;height:24px">Name*</div>
    <div class="field" style="left:376px;top:3303px;width:208px;height:24px">Email*</div>
    <div class="field" style="left:159px;top:3340px;width:208px;height:24px">Phone No.</div>
    <div class="field" style="left:376px;top:3340px;width:208px;height:24px">Address</div>
    <div class="field message" style="left:159px;top:3374px;width:425px;height:96px">Message</div>
    <div class="pill" style="left:333px;top:3485px;width:75px;height:26px">Send</div>
  </form>

  <!-- Footer -->
  <footer>
    <div class="abs brand" style="left:171px;top:3654px;font-size:24px;">TREAT<br>LOFT</div>
    <p class="abs copy" style="left:171px;top:3704px;width:200px;font-size:6.5px;color:#4a3a2a">Popcorn, ice cream and shakes made by hand in small batches, packed in tins and bags that make every visit a little sweeter.</p>
    <div class="abs foot-title" style="left:365px;top:3666px">QUICK LINKS</div>
    <ul class="abs foot-links" style="left:365px;top:3690px">
      <li>Home</li><li>About Us</li><li>Menu</li><li>Gift/Promotion</li><li>Contact Us</li>
    </ul>
    <div class="abs foot-title" style="left:500px;top:3666px">CONNECT US</div>
    <div class="abs social" style="left:500px;top:3694px"><i></i><i></i><i></i></div>
    <p class="abs copy" style="left:500px;top:3708px;width:110px;font-size:6px;color:#4a3a2a">Treat Loft Copyright<br>© 2019</p>
  </footer>
</section>

</body>
</html>
```